Employee Benefits and Insurance Consulting

We are an existing company with over 30 years experience but are changing our name. We would like a simple design with grey tones.

Industry/Entity Type

Insurance

Contact Information for Business Card

Marlow Benefits Consulting
Gerald P Hollins CEO
5172 Brackenridge Road
Kingsbury, TN 37912
gerald@marlowbenefits-example.com
865-412-5593 - O
865-247-3861 - C

```html
<!DOCTYPE html>
<html lang="en">
<head>
<meta charset="utf-8">
<title>Marlow Benefits Consulting – Business Card</title>
<link rel="stylesheet" href="https://fonts.googleapis.com/css2?family=Open+Sans:wght@400;600;700&display=swap">
<style>
  :root {
    --brand-red: #d71920;
    --rule-red: #eb8f92;
    --ink: #262626;
    --card: #ffffff;
    --backdrop: #e8e6e3;
  }
  * { margin: 0; padding: 0; box-sizing: border-box; }
  html, body {
    width: 1200px; height: 900px; overflow: hidden;
    background: var(--backdrop);
    font-family: "Open Sans", Arial, sans-serif;
  }
  .canvas { position: relative; width: 1200px; height: 900px; }

  .card {
    position: absolute;
    background: var(--card);
    box-shadow: 0 6px 18px rgba(0,0,0,0.12);
    overflow: hidden;
  }
  .card--front { left: 77px; top: 33px; width: 588px; height: 365px; }
  .card--back  { left: 388px; top: 505px; width: 567px; height: 352px; }

  /* Front */
  .side-band {
    position: absolute; left: 30px; top: 0;
    width: 126px; height: 100%;
    background: var(--brand-red);
  }
  .band-circle {
    position: absolute; left: 1px; top: 29px;
    width: 124px; height: 124px; border-radius: 50%;
    background: var(--card);
  }
  .brand-name {
    position: absolute; left: 175px; top: 56px;
    color: var(--brand-red);
    font-weight: 700; font-size: 31px; line-height: 1.12;
    letter-spacing: -0.2px;
  }
  .person {
    position: absolute; left: 176px; top: 164px;
    color: var(--brand-red);
    font-weight: 600; font-size: 20px;
  }
  .person .title { font-size: 15px; }
  .rule {
    position: absolute; left: 176px; width: 190px; height: 1.5px;
    background: var(--rule-red);
  }
  .rule--top { top: 205px; }
  .rule--bottom { top: 265px; }
  .address {
    position: absolute; left: 176px; top: 215px;
    color: var(--ink); font-size: 15.5px; line-height: 22px;
    font-style: normal;
  }
  .contacts {
    position: absolute; left: 138px; top: 274px;
    list-style: none;
    color: var(--ink); font-size: 15.5px; line-height: 24px;
  }
  .contacts li { display: flex; align-items: center; }
  .contacts svg { width: 12px; height: 12px; margin-right: 26px; flex: none; }

  /* Back */
  .back-name {
    position: absolute; left: 20px; right: 0; top: 148px;
    text-align: center;
    color: var(--brand-red);
    font-weight: 700; font-size: 32px;
    letter-spacing: -0.2px;
  }
</style>
</head>
<body>
<main class="canvas">

  <section class="card card--front" aria-label="Business card front">
    <div class="side-band"><div class="band-circle"></div></div>
    <div class="brand-name">Marlow Benefits<br>Consulting</div>
    <div class="person">Gerald P Hollins <span class="title">- CEO</span></div>
    <div class="rule rule--top"></div>
    <address class="address">
      5172 Brackenridge Road<br>Kingsbury, TN 37912
    </address>
    <div class="rule rule--bottom"></div>
    <ul class="contacts">
      <li>
        <svg viewBox="0 0 12 12" aria-hidden="true"><path fill="#fff" d="M2.4 1l2 2.2-1 1.2c.7 1.6 1.7 2.6 3.2 3.3l1.2-1 2.2 2-1 1.6C5.3 10.2 1.8 6.7 1 2.3z"/></svg>
        865-412-5593
      </li>
      <li>
        <svg viewBox="0 0 12 12" aria-hidden="true"><rect x="3" y="0.5" width="6" height="11" rx="1" fill="none" stroke="#fff" stroke-width="1.2"/><rect x="5.2" y="9" width="1.6" height="1" fill="#fff"/></svg>
        865-247-3861
      </li>
      <li>
        <svg viewBox="0 0 12 12" aria-hidden="true"><rect x="0.5" y="2.5" width="11" height="7" fill="#fff"/><path d="M0.5 2.5l5.5 4 5.5-4" fill="none" stroke="#d71920" stroke-width="1"/></svg>
        gerald@marlowbenefits-example.com
      </li>
    </ul>
  </section>

  <section class="card card--back" aria-label="Business card back">
    <div class="back-name">Marlow Benefits Consulting</div>
  </section>

</main>
</body>
</html>
```